Website Design Request - Management Consulting Firm

We need a Website designed for an IT Management Staffing and Recruiting firm called TRAVENOK based in San Francisco.

The firm is an high-end technology staffing agency. Our focus is on quality and high-caliber candidates rather than quantity.

The website will have two main home pages. One for the recruiter and another on for the candidates.

The website needs to optimize for mobile devices as well.

I have attached few mock-ups that I have done just to show what I am thinking. The UI needs to be very clean, fluid, and it needs to have a modern, rustic, professional feel to it.

Target Market(s)

Technology Manager, Director, VP, CIO of Companies that have $4b-10b dollar revenue. Such as larkspurdwellings.example , https://www.velmorian.example/, quillnet.example, zib.example

Industry/Entity Type

Management Consulting

Number of Pages Required

5+ page

Font styles to use
Sans Serif

Colors
f37122
ffffff

Requirements
Must have
• Please review mock-ups for suggestions
Nice to have
Should not have

```html
<!DOCTYPE html>
<html lang="en">
<head>
<meta charset="utf-8">
<title>TRAVENOK — IT Project Management Jobs</title>
<link href="https://fonts.googleapis.com/css2?family=Raleway:wght@400;600;700;800&family=Open+Sans:wght@400;600&display=swap" rel="stylesheet">
<style>
:root{
  --orange:#f37122;
  --orange-dark:#de621b;
  --ink:#444444;
  --body:#777777;
  --white:#ffffff;
  --footer-bg:#f2f2f2;
  --footer-ink:#8a8a8a;
  --social:#c9c9c9;
}
*{margin:0;padding:0;box-sizing:border-box}
html,body{width:922px;height:1200px;overflow:hidden;background:var(--white)}
body{position:relative;font-family:"Open Sans",Arial,sans-serif;color:var(--body)}
.abs{position:absolute}

/* header */
.site-header{position:absolute;left:0;top:0;width:922px;height:61px;background:var(--white)}
.brand{position:absolute;left:76px;top:10px}
.brand-name{font-family:"Raleway",sans-serif;font-weight:700;font-size:25px;letter-spacing:1px;color:var(--orange);line-height:28px}
.brand-tag{font-family:"Open Sans",sans-serif;font-size:6.5px;letter-spacing:.4px;color:#333;margin-top:1px}
.main-nav a{position:absolute;top:27px;font-family:"Raleway",sans-serif;font-size:9.5px;color:#333;text-decoration:none;letter-spacing:.2px}

/* hero */
.hero{position:absolute;left:0;top:61px;width:922px;height:364px;overflow:hidden}
.hero-photo{position:absolute;inset:0;background:
  radial-gradient(ellipse at 72% 55%,#d9d6d0 0%,#a8a49d 28%,rgba(60,58,56,.2) 60%),
  linear-gradient(120deg,#1b1b1b 0%,#3a3532 35%,#6b6660 60%,#2a2928 100%)}
.hero-shade{position:absolute;inset:0;background:rgba(0,0,0,.28)}
.hero-title{position:absolute;left:0;width:922px;top:135px;text-align:center;font-family:"Raleway",sans-serif;font-weight:700;font-size:21px;color:var(--white);letter-spacing:.3px}
.hero-sub{position:absolute;left:0;width:922px;top:170px;text-align:center;font-family:"Raleway",sans-serif;font-size:12.5px;color:var(--white)}
.btn{display:flex;align-items:center;justify-content:center;background:var(--orange);color:var(--white);font-family:"Raleway",sans-serif;font-weight:700;text-decoration:none;border-radius:2px}
.hero-cta{position:absolute;left:394px;top:208px;width:134px;height:34px;font-size:11px}
.hero-employers{position:absolute;left:0;width:922px;top:272px;text-align:center;font-size:9.5px;color:var(--white)}
.hero-employers strong{font-weight:600}
.dots{position:absolute;left:440px;top:340px;display:flex;gap:4px}
.dots span{width:7px;height:7px;border-radius:50%;background:rgba(255,255,255,.45)}
.dots span:first-child{background:var(--orange)}

/* tabs */
.tab{position:absolute;top:425px;height:66px;color:var(--white);text-align:center;font-family:"Raleway",sans-serif;font-size:10px}
.tab-how{left:0;width:461px;background:var(--orange)}
.tab-why{left:461px;width:461px;background:var(--orange-dark)}
.tab svg{position:absolute;left:50%;transform:translateX(-50%);top:11px}
.tab span{position:absolute;left:0;right:0;top:42px}

/* benefits */
.section-title{position:absolute;left:0;width:922px;top:550px;text-align:center;font-family:"Raleway",sans-serif;font-weight:700;font-size:23.5px;color:var(--ink)}
.benefit{position:absolute;width:270px;text-align:center}
.benefit svg{display:block;margin:0 auto}
.benefit h3{font-family:"Raleway",sans-serif;font-weight:700;font-size:10.5px;color:var(--ink);letter-spacing:.2px}
.benefit p{font-size:9.6px;line-height:17.6px;color:var(--body);margin-top:10px}
.upload{position:absolute;left:362px;top:1014px;width:199px;height:47px;font-size:11.5px;gap:9px}

/* footer */
.site-footer{position:absolute;left:0;top:1110px;width:922px;height:90px;background:var(--footer-bg);border-top:1px solid #e6e6e6;font-size:8.6px;color:var(--footer-ink)}
.site-footer a{color:var(--footer-ink);text-decoration:none}
.footer-links a{position:absolute;top:25px}
.footer-legal{position:absolute;left:76px;top:52px;display:flex;gap:13px}
.social{position:absolute;left:574px;top:35px;display:flex;align-items:center;gap:6px}
.social i{display:block;width:21px;height:21px;border-radius:50%;background:var(--social)}
.social span{margin-right:2px}
</style>
</head>
<body>

<header class="site-header">
  <div class="brand">
    <div class="brand-name">TRAVENOK</div>
    <div class="brand-tag">PROJECT MANAGEMENT CONSULTING</div>
  </div>
  <nav class="main-nav">
    <a href="#" style="left:490px">PROFESSIONAL</a>
    <a href="#" style="left:613px">EMPLOYERS</a>
    <a href="#" style="left:722px">SIGN IN</a>
    <a href="#" style="left:811px">SIGN UP</a>
  </nav>
</header>

<section class="hero">
  <div class="hero-photo" role="img" aria-label="Photo: team around a table reviewing printed charts and a tablet"></div>
  <div class="hero-shade"></div>
  <h1 class="hero-title">LOOKING FOR IT PROJECTS MANAGEMENT JOBS?</h1>
  <p class="hero-sub">UPLOAD YOUR RESUME, ACCEPT INTERVIEW REQUESTS, GET OFFERS</p>
  <a class="btn hero-cta" href="#">GET OFFERS NOW</a>
  <p class="hero-employers"><strong>Looking for talents?</strong> see how it works for employers</p>
  <div class="dots"><span></span><span></span><span></span><span></span></div>
</section>

<a class="tab tab-how" href="#" style="text-decoration:none">
  <svg width="26" height="24" viewBox="0 0 26 24" fill="none" stroke="#fff" stroke-width="2.2">
    <circle cx="9" cy="13" r="4.5" stroke-dasharray="2.5 1.2"/>
    <circle cx="9" cy="13" r="1.5" fill="#fff"/>
    <circle cx="19" cy="6" r="3.2" stroke-dasharray="2 1"/>
    <circle cx="19.5" cy="19" r="2.8" stroke-dasharray="2 1"/>
  </svg>
  <span>HOW IT WORKS?</span>
</a>
<a class="tab tab-why" href="#" style="text-decoration:none">
  <svg width="24" height="24" viewBox="0 0 24 24" fill="none" stroke="#fff" stroke-width="1.3">
    <path d="M2 2h20v15h-8l-2 4-2-4H2z"/>
    <text x="12" y="14" text-anchor="middle" font-family="Raleway,sans-serif" font-weight="700" font-size="10" fill="#fff" stroke="none">?</text>
  </svg>
  <span>WHY US?</span>
</a>

<h2 class="section-title">WHY PROFESSIONALS LOVE US</h2>

<div class="benefit" style="left:142px;top:622px">
  <svg width="56" height="58" viewBox="0 0 56 58" fill="none" stroke="#f37122" stroke-width="1.4">
    <path d="M17 1h14v16h15v8H36M31 41H17V27H1V17h16z"/>
    <circle cx="39" cy="40" r="12"/>
    <text x="39" y="46" text-anchor="middle" font-family="Open Sans,sans-serif" font-size="16" fill="none" stroke="#f37122" stroke-width=".9">$</text>
  </svg>
  <h3 style="margin-top:22px">GET PAID MORE</h3>
  <p>On average,TRAVENOK candidates get upto 20% more for their skills. Our talent makkes you discoverable for your niche project experiences.</p>
</div>

<div class="benefit" style="left:511px;top:622px">
  <svg width="70" height="58" viewBox="0 0 70 58" fill="none" stroke="#f37122" stroke-width="1.3">
    <path d="M1 1h40v24H34M20 25H10l-4 7V25H1z"/>
    <path d="M21 21h48v27H57l-3 9-3-9H21z"/>
    <g fill="#f37122" stroke="none"><circle cx="15" cy="13" r="1.3"/><circle cx="21" cy="13" r="1.3"/><circle cx="27" cy="13" r="1.3"/><circle cx="38" cy="34" r="1.3"/><circle cx="45" cy="34" r="1.3"/><circle cx="52" cy="34" r="1.3"/></g>
  </svg>
  <h3 style="margin-top:22px">LESS INTERVIEWS</h3>
  <p>On average,TRAVENOK candidates get upto 20% more for their skills. Our talent makkes you discoverable for your niche project experiences.</p>
</div>

<div class="benefit" style="left:142px;top:820px">
  <svg width="44" height="42" viewBox="0 0 44 42" fill="none" stroke="#f37122" stroke-width="1.1">
    <path d="M1 9h33v32H1zM10 1h33v32H10zM1 9l9-8M34 9l9-8M34 41l9-8M1 41l9-8"/>
  </svg>
  <h3 style="margin-top:26px">TRANSPERENCY</h3>
  <p>On average,TRAVENOK candidates get upto 20% more for their skills. Our talent makkes you discoverable for your niche project experiences.</p>
</div>

<div class="benefit" style="left:511px;top:810px">
  <svg width="48" height="54" viewBox="0 0 48 54" fill="none" stroke="#f37122" stroke-width="1.6" stroke-linejoin="round">
    <path d="M13 24h-10v28h10zM13 26l10-14c2-4 2-9 4-11 4 0 5 4 4 9l-2 9h14c3 0 5 3 3 6 2 1 2 5 0 6 2 2 1 5-1 6 1 3-1 6-4 6H17l-4-3"/>
  </svg>
  <h3 style="margin-top:24px">MAKE BETTER DECISIONS</h3>
  <p>On average,TRAVENOK candidates get upto 20% more for their skills. Our talent makkes you discoverable for your niche project experiences.</p>
</div>

<a class="btn upload" href="#">
  <svg width="22" height="20" viewBox="0 0 22 20" fill="#fff">
    <path d="M11 0l6 6h-4v7H9V6H5z"/>
    <path d="M0 11h3v6h16v-6h3v9H0z"/>
  </svg>
  UPLOAD YOUR RESUME
</a>

<footer class="site-footer">
  <nav class="footer-links">
    <a href="#" style="left:76px">Professional</a>
    <a href="#" style="left:160px">Employers</a>
    <a href="#" style="left:238px">Sign In</a>
    <a href="#" style="left:300px">Sign Up</a>
  </nav>
  <div class="footer-legal">
    <span>© 2016. Travenok. All rights reserved.</span>
    <a href="#">Privacy Policy</a><span>/</span>
    <a href="#">Terms &amp; Conditions</a><span>/</span>
    <a href="#">Disclaimer</a>
  </div>
  <div class="social">
    <span>Connect with our social network :</span>
    <i></i><i style="margin-left:1px"></i><i></i><i></i><i></i>
  </div>
</footer>

</body>
</html>
```